Beilege-Broschüre Online Versand Stuetzwerk.de
Zielgruppe
Bandagen, Orthesen und Sport-Schutzprodukte
Zielgruppe Menschen mit Verletzungen, Sportler und ältere Menschen.
Aufgabenstellung
Vorlage vorhanden und Format bereits festgelegt. Es geht um die kreative Umsetzung der gewünschten Inhalte und Vorbereitung zum druckfähigen Produkt.
Es handelt sich um einen Beileger für Versendungen im Online Bereich. Dieser soll unser Produktportfolio aufzeigen und mit vorhandenem Bildmaterial und Vorlagen erarbeitet werden.
eine INDD Vorlage steht zur Verfügung.

```html
<!DOCTYPE html>
<html lang="de">
<head>
<meta charset="utf-8">
<title>Stuetzwerk.de – Flexibel Stabilität</title>
<link rel="stylesheet" href="https://fonts.googleapis.com/css2?family=Lato:wght@100;400&display=swap">
<style>
  :root {
    --paper: #ffffff;
    --stage-dark: #111213;
    --stage-mid: #34363a;
    --stage-floor: #55585c;
    --text-light: #ffffff;
    --bandage-light: #9a9c9f;
    --bandage-dark: #2a2b2d;
    --athlete-warm: #7a5c4a;
    --athlete-dark: #1d1e20;
    --kettlebell: #d8b82a;
  }
  html, body {
    margin: 0;
    padding: 0;
    width: 1200px;
    height: 846px;
    overflow: hidden;
    background: var(--paper);
  }
  .flyer {
    position: relative;
    width: 1200px;
    height: 846px;
    overflow: hidden;
    background: var(--paper);
    font-family: "Lato", "Helvetica Neue", Arial, sans-serif;
  }
  .stage {
    position: absolute;
    left: 30px;
    top: 0;
    right: 0;
    bottom: 0;
    background:
      radial-gradient(ellipse 55% 45% at 60% 92%, var(--stage-floor) 0%, transparent 70%),
      radial-gradient(ellipse 60% 55% at 62% 40%, var(--stage-mid) 0%, transparent 75%),
      var(--stage-dark);
  }
  .product-visual {
    position: absolute;
    left: 199px;
    top: 0;
    width: 402px;
    height: 455px;
    border-radius: 0 0 8px 8px;
    background: linear-gradient(160deg, var(--bandage-dark) 0%, var(--bandage-light) 48%, #5b5d60 70%, var(--bandage-dark) 100%);
  }
  .athlete-visual {
    position: absolute;
    left: 543px;
    top: 175px;
    width: 450px;
    height: 583px;
    border-radius: 8px;
    background: linear-gradient(200deg, var(--kettlebell) 0%, var(--kettlebell) 14%, var(--athlete-warm) 30%, #4a3c33 60%, var(--athlete-dark) 100%);
  }
  .headline {
    position: absolute;
    left: 80px;
    top: 430px;
    margin: 0;
    color: var(--text-light);
    font-family: "Lato", "Helvetica Neue", Arial, sans-serif;
    font-weight: 100;
    font-size: 152px;
    line-height: 180px;
    letter-spacing: 4px;
    text-transform: uppercase;
  }
  .headline span { display: block; }
  .brand {
    position: absolute;
    left: 968px;
    top: 772px;
    display: flex;
    align-items: center;
    gap: 12px;
    color: var(--text-light);
    font-family: "Lato", "Helvetica Neue", Arial, sans-serif;
    font-weight: 400;
    font-size: 24px;
  }
  .brand-dot {
    width: 34px;
    height: 34px;
    border-radius: 50%;
    background: var(--text-light);
  }
</style>
</head>
<body>
  <main class="flyer">
    <div class="stage"></div>
    <div class="product-visual" role="img" aria-label="Nahaufnahme einer grau-schwarzen Strickbandage am Gelenk"></div>
    <div class="athlete-visual" role="img" aria-label="Sportler in schwarzen Shorts stemmt eine gelbe Kettlebell über den Kopf"></div>
    <h1 class="headline">
      <span>Flexibel</span>
      <span>Stabilität</span>
    </h1>
    <div class="brand">
      <span class="brand-dot"></span>
      <span class="brand-name">Stuetzwerk.de</span>
    </div>
  </main>
</body>
</html>
```